TalkHarbor - Language Coaching Services

Sleek, innovative, trendy design for Language Coaching business.

TalkHarbor is a new UK based company that provides Language Coaching services. We offer highly personalized on-line and face to face language courses. We also impart learning techniques workshops based on the latest neuroscience research for second-language acquisition.

Target Market(s)

See attached info

Industry/Entity Type

Consulting

Contact Information for Business Card

TalkHarbor
DaniaKV@talkharbor.co.uk
TalkHarbor.co.uk
London, UK

Font styles to use
Sans Serif

```html
<!DOCTYPE html>
<html lang="en">
<head>
<meta charset="utf-8">
<title>TalkHarbor – Business Card</title>
<link rel="stylesheet" href="https://fonts.googleapis.com/css2?family=Montserrat:wght@400;600&family=Lato:wght@400&display=swap">
<style>
  :root {
    --backdrop: #666666;
    --card-white: #ffffff;
    --brand-blue: #0a97d3;
    --brand-blue-deep: #0079b3;
    --brand-blue-light: #00aae2;
    --text-grey: #444a4f;
    --divider: #9fd3ee;
    --shadow: rgba(0, 0, 0, 0.45);
  }
  * { margin: 0; padding: 0; box-sizing: border-box; }
  html, body {
    width: 1200px; height: 900px; overflow: hidden;
    background: var(--backdrop);
  }
  .stage { position: relative; width: 1200px; height: 900px; }

  .card {
    position: absolute; top: 275px;
    width: 477px; height: 294px;
    box-shadow: 2px 3px 5px var(--shadow);
  }
  .card--front {
    left: 120px;
    background: var(--card-white);
    border-radius: 0 52px 0 52px;
  }
  .card--back {
    left: 620px;
    border-radius: 52px 0 52px 0;
    background: linear-gradient(135deg,
      var(--brand-blue-deep) 0%,
      var(--brand-blue-light) 35%,
      var(--brand-blue-light) 55%,
      var(--brand-blue-deep) 100%);
  }

  /* front: brand spot */
  .brand-spot {
    position: absolute; left: 68px; top: 74px;
    width: 142px; height: 142px;
    display: flex; align-items: center; justify-content: center;
  }
  .brand-spot__ring {
    position: absolute; inset: 0;
    border: 10px solid var(--brand-blue);
    border-radius: 50%;
  }
  .brand-spot__name {
    font-family: "Montserrat", sans-serif; font-weight: 600;
    font-size: 17px; color: var(--brand-blue);
  }

  .divider {
    position: absolute; left: 238px; top: 83px;
    width: 1px; height: 122px; background: var(--divider);
  }

  .details {
    position: absolute; left: 266px; top: 82px;
    font-family: "Lato", sans-serif; color: var(--text-grey);
  }
  .details__name {
    font-family: "Montserrat", sans-serif; font-size: 17px;
    color: var(--brand-blue); line-height: 20px; letter-spacing: 0.2px;
  }
  .details__name strong { font-weight: 600; }
  .details__name span { font-weight: 400; }
  .details__role { font-size: 14px; line-height: 17px; }
  .details__city { font-size: 14px; margin-top: 9px; line-height: 17px; }
  .contact-list { list-style: none; margin-top: 12px; }
  .contact-list li {
    display: flex; align-items: center; gap: 4px;
    font-size: 13.5px; line-height: 17px;
  }
  .contact-list svg { width: 11px; height: 11px; flex: none; }

  /* back: wordmark */
  .wordmark {
    position: absolute; left: 0; right: 0; top: 78px;
    display: flex; flex-direction: column; align-items: center;
  }
  .wordmark__circle {
    width: 100px; height: 100px;
    border: 7px solid var(--card-white); border-radius: 50%;
  }
  .wordmark__name {
    margin-top: 6px;
    font-family: "Montserrat", sans-serif; font-weight: 400;
    font-size: 38px; letter-spacing: 0.5px;
    color: var(--card-white);
  }
</style>
</head>
<body>
<main class="stage">
  <section class="card card--front" aria-label="Business card front">
    <div class="brand-spot">
      <div class="brand-spot__ring"></div>
      <span class="brand-spot__name">TalkHarbor</span>
    </div>
    <div class="divider"></div>
    <div class="details">
      <p class="details__name"><strong>OLIVER</strong> <span>BRANTLEY</span></p>
      <p class="details__role">Managing Director</p>
      <p class="details__city">London, UK</p>
      <ul class="contact-list">
        <li>
          <svg viewBox="0 0 12 12" aria-hidden="true"><rect x="2.5" y="0.8" width="7" height="10.4" rx="1.3" fill="none" stroke="#0a97d3" stroke-width="1.5"/><rect x="5" y="8.6" width="2" height="1" fill="#0a97d3"/></svg>
          044 555 0142
        </li>
        <li>
          <svg viewBox="0 0 12 12" aria-hidden="true"><rect x="0.5" y="2.5" width="11" height="7.5" fill="#0a97d3"/><path d="M0.8 2.8 6 6.8 11.2 2.8" fill="none" stroke="#fff" stroke-width="1"/></svg>
          DaniaKV@talkharbor.co.uk
        </li>
        <li>
          <svg viewBox="0 0 12 12" aria-hidden="true"><circle cx="6" cy="6" r="5.5" fill="#0a97d3"/><path d="M3 4.5c1-1 2 0 2.5 1s-.5 2 .5 3M7.5 2.5c.5 1 2 1 2.5 2" fill="none" stroke="#fff" stroke-width="1"/></svg>
          www.TalkHarbor.co.uk
        </li>
      </ul>
    </div>
  </section>

  <section class="card card--back" aria-label="Business card back">
    <div class="wordmark">
      <div class="wordmark__circle"></div>
      <p class="wordmark__name">TALKHARBOR</p>
    </div>
  </section>
</main>
</body>
</html>
```